Modern looking signage for dental office.

Exterior signage for passing cars
Updates
Need extra days to review
Target Market(s)
Cars passing by
Font styles to use
Sans Serif
Colors
3276b5
Requirements
Must have
- Logo
- OPEN ON SUTURDAY AND SUNDAY
- NIGHT CLINIC AVAILABLE
- PLEASE USE THE FONT TYPE IN FILE 4 UPLOADED BELOW.
- (847) 302-7469
- Modern looking

```html
<!DOCTYPE html>
<html lang="en">
<head>
<meta charset="utf-8">
<title>Alderwick Dental – Weekend Night Clinic Sign</title>
<link rel="stylesheet" href="https://fonts.googleapis.com/css2?family=Open+Sans:wght@400;700&family=Raleway:wght@400&display=swap">
<style>
  :root {
    --teal: #11869e;
    --white: #ffffff;
    --ink: #444444;
    --phone-grey: #666666;
    --swoosh-light: #f2f2f2;
    --swoosh-dark: #b9b9b9;
    --backdrop: #eceeef;
  }
  * { margin: 0; padding: 0; box-sizing: border-box; }
  html, body { width: 1200px; height: 2311px; overflow: hidden; }
  body { background: var(--backdrop); font-family: "Open Sans", Arial, sans-serif; }

  .sign {
    position: absolute; left: 50px; top: 605px;
    width: 1100px; height: 1100px;
    background: var(--white);
    box-shadow: 0 10px 30px rgba(0,0,0,0.18);
    overflow: hidden;
  }
  .sign-shapes { position: absolute; inset: 0; }
  .line { position: absolute; left: 0; width: 100%; text-align: center; line-height: 1; white-space: nowrap; }

  .brand-mark {
    position: absolute; left: 168px; top: 48px;
    width: 156px; height: 156px; border-radius: 50%;
    border: 3px solid var(--ink);
  }
  .brand-name {
    position: absolute; left: 345px; top: 80px;
    font-family: "Raleway", Arial, sans-serif; font-weight: 400;
    font-size: 70px; line-height: 1; color: var(--ink); letter-spacing: 1px;
    white-space: nowrap;
  }
  .brand-tagline {
    position: absolute; left: 345px; top: 176px; width: 640px; text-align: center;
    font-size: 29px; color: var(--ink); line-height: 1;
  }

  .open-on { top: 453px; font-size: 66px; font-weight: 700; color: var(--white); }
  .days { top: 522px; font-size: 90px; font-weight: 700; color: var(--white); }
  .clinic-from { top: 659px; font-size: 45px; color: var(--white); }
  .hours { top: 719px; font-size: 86px; font-weight: 700; color: var(--white); }
  .available { top: 828px; font-size: 45px; color: var(--white); }

  .rule { position: absolute; left: 240px; width: 620px; height: 2px; background: rgba(255,255,255,0.6); }
  .rule-top { top: 714px; }
  .rule-bottom { top: 812px; }

  .phone {
    position: absolute; left: 0; width: 100%; top: 936px;
    display: flex; justify-content: center; align-items: center; gap: 18px;
  }
  .phone-icon { width: 84px; height: 84px; }
  .phone-number { font-size: 122px; font-weight: 700; color: var(--phone-grey); line-height: 1; }
</style>
</head>
<body>
  <main class="sign">
    <svg class="sign-shapes" width="1100" height="1100" viewBox="0 0 1100 1100" aria-hidden="true">
      <defs>
        <linearGradient id="swoosh" x1="0" y1="0" x2="1" y2="0">
          <stop offset="0" stop-color="var(--swoosh-light)"/>
          <stop offset="0.5" stop-color="var(--swoosh-dark)"/>
          <stop offset="1" stop-color="var(--swoosh-light)"/>
        </linearGradient>
      </defs>
      <path d="M0,443 Q560,140 1100,337 L1100,372 Q560,190 0,464 Z" fill="url(#swoosh)"/>
      <path d="M0,464 Q560,190 1100,372 L1100,917 L0,917 Z" fill="var(--teal)"/>
    </svg>

    <div class="brand-mark"></div>
    <div class="brand-name">ALDERWICK DENTAL</div>
    <div class="brand-tagline">MODERN GENERAL DENTISTRY</div>

    <div class="line open-on">OPEN ON</div>
    <div class="line days">SATURDAY &amp; SUNDAY</div>
    <div class="line clinic-from">NIGHT CLINIC FROM</div>
    <div class="rule rule-top"></div>
    <div class="line hours">5PM TO 10PM</div>
    <div class="rule rule-bottom"></div>
    <div class="line available">AVAILABLE</div>

    <div class="phone">
      <svg class="phone-icon" viewBox="0 0 64 64" aria-hidden="true">
        <path d="M16 6c3 0 9 10 9 13s-5 4-5 7c0 5 13 18 18 18 3 0 4-5 7-5s13 6 13 9c0 5-6 11-12 11C27 59 5 37 5 18 5 12 11 6 16 6z" fill="var(--teal)"/>
        <path d="M36 18a10 10 0 0 1 10 10M36 10a18 18 0 0 1 18 18M36 2a26 26 0 0 1 26 26" fill="none" stroke="var(--teal)" stroke-width="3.5" stroke-linecap="round"/>
      </svg>
      <span class="phone-number">847 302 7469</span>
    </div>
  </main>
</body>
</html>
```